Harrow Grading LLC business card design

Excavation company business cards

Contact Information for Business Card

Harrow Grading LLC cell phone 208-417-6290 office phone 208-319-4856 harrowgradingllc@maplecove.com Driveways, site prep, retaining walls, septic systems, rock delivery

Colors

Designer to choose colors to be used in the design.

```html
<!DOCTYPE html>
<html lang="en">
<head>
<meta charset="utf-8">
<title>Harrow Grading LLC – Business Card</title>
<link href="https://fonts.googleapis.com/css2?family=Michroma&family=Poppins:wght@400&display=swap" rel="stylesheet">
<style>
  :root {
    --page-bg: #e6e6e6;
    --card-white: #ffffff;
    --brand-orange: #ec6f24;
    --brand-orange-light: #ef7d30;
    --ink: #1f1f1f;
    --steel: #3a3a3a;
    --bar-grey: #6b6b6b;
    --faint-orange: #fbe3d3;
    --faint-grey: #efefef;
  }
  * { margin: 0; padding: 0; box-sizing: border-box; }
  html, body { width: 1200px; height: 1200px; overflow: hidden; }
  body { background: var(--page-bg); position: relative; font-family: "Poppins", sans-serif; }

  .card {
    position: absolute;
    left: 257px;
    width: 686px;
    height: 392px;
    overflow: hidden;
  }
  .card--front { top: 165px; background: var(--card-white); }
  .card--back {
    top: 653px;
    background: linear-gradient(180deg, var(--brand-orange-light), var(--brand-orange));
  }

  .brand-decoration { position: absolute; left: 338px; top: 18px; width: 348px; height: 374px; }

  .brand-name {
    font-family: "Michroma", sans-serif;
    font-weight: 400;
    white-space: nowrap;
  }
  .card--front .brand-name {
    position: absolute;
    left: 60px;
    top: 140px;
    font-size: 20px;
    color: var(--brand-orange);
  }

  .edge-bar { position: absolute; left: 0; top: 264px; width: 11px; height: 68px; background: var(--bar-grey); }

  .contact-list { position: absolute; left: 62px; top: 256px; list-style: none; }
  .contact-list li {
    display: flex; align-items: center; gap: 9px;
    height: 19.7px; font-size: 14.5px; color: var(--ink); white-space: nowrap;
  }
  .contact-list svg { width: 11px; height: 11px; fill: var(--brand-orange); flex: none; }

  .name-band { position: absolute; left: 355px; top: 265px; width: 331px; height: 67px; }
  .name-band svg { position: absolute; inset: 0; }
  .person-name {
    position: absolute; right: 30px; top: 14px;
    font-family: "Michroma", sans-serif; font-size: 18.5px; color: #fff; letter-spacing: 0.5px;
  }
  .person-title {
    position: absolute; right: 30px; top: 39px;
    font-size: 14px; color: #fff; letter-spacing: 0.4px;
  }

  .card--back .brand-name {
    position: absolute; left: 0; right: 0; top: 224px;
    text-align: center; font-size: 21px; color: var(--steel);
  }
</style>
</head>
<body>
  <section class="card card--front">
    <svg class="brand-decoration" role="img" aria-label="Faint large brand decoration area" viewBox="0 0 348 374">
      <defs>
        <linearGradient id="faintFade" x1="0" y1="0" x2="1" y2="1">
          <stop offset="0" stop-color="var(--faint-grey)"/>
          <stop offset="1" stop-color="var(--faint-orange)"/>
        </linearGradient>
      </defs>
      <rect x="0" y="0" width="348" height="374" fill="url(#faintFade)" opacity="0.55"/>
    </svg>

    <div class="brand-name">Harrow Grading LLC</div>

    <div class="edge-bar"></div>
    <ul class="contact-list">
      <li><svg viewBox="0 0 12 12"><path d="M2.4 0.8 4.2 2.9 3.3 4.3c.8 1.7 2.1 3 3.9 3.9l1.4-.9 2.1 1.8-1.1 2.1C5 10.8 1.3 7 .4 2.2z"/></svg>208-319-4856</li>
      <li><svg viewBox="0 0 12 12"><path d="M3 0h6a1 1 0 0 1 1 1v10a1 1 0 0 1-1 1H3a1 1 0 0 1-1-1V1a1 1 0 0 1 1-1zm.6 1.2v8.6h4.8V1.2zM6 10.3a.6.6 0 1 0 0 1.2.6.6 0 0 0 0-1.2z"/></svg>208-417-6290</li>
      <li><svg viewBox="0 0 12 12"><path d="M0 3h12v7H0zm1 .8 5 3.4 5-3.4v-.1H1z"/></svg>harrowgradingllc@maplecove.com</li>
      <li><svg viewBox="0 0 12 12"><circle cx="6" cy="6" r="5.6"/></svg>Harrowgradingllc.com</li>
    </ul>

    <div class="name-band">
      <svg viewBox="0 0 331 67" preserveAspectRatio="none"><polygon points="47,0 331,0 331,67 0,67" fill="var(--brand-orange)"/></svg>
      <div class="person-name">DANIEL REEVE</div>
      <div class="person-title">President</div>
    </div>
  </section>

  <section class="card card--back">
    <div class="brand-name">Harrow Grading LLC</div>
  </section>
</body>
</html>
```